Business software developers new website

We need to redesign our website. Our current website is http://www.plovencast.example/index.html, which is outdated and needs a new look. We moved out from web design and have concentrated more on the back end of the systems, for example, system support and security and cloud-based applications. Our major clients include both private and government sectors. We would like to see some designs that are all in one page, simple and clean. Prefer illustrator or obstructed images instead of real-life photos. Must look futuristic yet friendly. Attached the new logo for your references and good luck.

Target Market(s)

Medium to big company for their IT or data management. Either improve or upgrade their current system.

Industry/Entity Type

Business Software

Number of Pages Required

1 page

Colors

Designer to choose colors to be used in the design.

Requirements
Must have
• Simple and clean. Individual assets must be provided in the correct size and format(png or jpeg). Prefer Goggle fonts. Even though the logo color is red, grey and black, still prefer some modern colors that go well with red. When design, must consider the possibility to convert it into responsive.
Nice to have
• White background
Should not have
• real life photos, no slider

```html
<!DOCTYPE html>
<html lang="en">
<head>
<meta charset="utf-8">
<title>Plovencast — Innovative &amp; High-Grade Software</title>
<link rel="stylesheet" href="https://fonts.googleapis.com/css2?family=Lato:wght@400;700;900&family=Roboto:ital,wght@0,400;0,500;0,700;1,400&display=swap">
<style>
:root{
  --red:#e8333f;
  --orange:#ff7a12;
  --ink:#1b1b1b;
  --text:#666;
  --muted:#8a8a8a;
  --soft:#f7f7f7;
  --line:#e6e6e6;
  --footer:#1c1c1c;
  --ghost:rgba(0,0,0,.05);
  --brand-grad:linear-gradient(90deg,var(--red) 0%,var(--orange) 100%);
}
*{box-sizing:border-box;margin:0;padding:0}
html,body{width:1200px;height:4199px;overflow:hidden}
body{position:relative;background:#fff;font-family:"Roboto",sans-serif;color:var(--text)}
.abs{position:absolute}
a{color:inherit;text-decoration:none}
ul{list-style:none}

/* header */
.topline{left:0;top:0;width:1200px;height:4px;background:var(--red)}
.logo{display:flex;align-items:center;gap:8px;font-family:"Roboto",sans-serif;font-weight:400;color:var(--ink);white-space:nowrap}
.logo-dot{width:30px;height:30px;border-radius:50%;background:var(--red)}
.site-logo{left:110px;top:42px;font-size:42px;letter-spacing:-.5px}
.main-nav{left:507px;top:54px;display:flex;gap:26px;font-size:16px;font-weight:500;color:var(--ink)}
.login{left:970px;top:46px;width:117px;height:35px;border-radius:18px;background:var(--red);color:#fff;font-size:15px;font-weight:700;display:flex;align-items:center;justify-content:center;gap:6px}
.login i{width:9px;height:11px;background:#fff;border-radius:2px;display:block}

/* hero */
.hero{left:0;top:121px;width:1200px;height:600px;background:var(--brand-grad);overflow:hidden}
.hero-wave{left:0;width:1200px}
.hero h1{left:112px;top:150px;width:520px;font-family:"Lato",sans-serif;font-weight:700;font-size:40px;line-height:47px;color:#fff}
.hero p{left:112px;top:272px;width:420px;font-size:16px;line-height:26px;color:#fff}
.btn{display:flex;align-items:center;justify-content:center;gap:6px;border-radius:25px;font-size:15px;font-weight:700;color:var(--red);background:#fff}
.btn .arrow{width:13px;height:13px;border-radius:50%;background:var(--red);position:relative}
.btn .arrow::after{content:"";position:absolute;left:4px;top:3px;border-left:5px solid #fff;border-top:3.5px solid transparent;border-bottom:3.5px solid transparent}
.hero .btn{left:112px;top:355px;width:198px;height:48px}
.hero-art{left:640px;top:100px;width:490px;height:410px;border-radius:16px;background:linear-gradient(135deg,rgba(255,255,255,.28),rgba(255,255,255,.08))}

/* section titles */
.ghost{font-family:"Lato",sans-serif;font-weight:900;color:var(--ghost);white-space:nowrap;letter-spacing:2px}
.title{font-family:"Lato",sans-serif;font-weight:700;color:var(--ink);white-space:nowrap}
.center{left:0;width:1200px;text-align:center}

/* about */
.about-art{left:0;top:780px;width:590px;height:400px;border-radius:20px;background:linear-gradient(135deg,#fbe3e3,#fff1e6)}
.about-ghost{left:630px;top:808px;font-size:82px}
.about-title{left:632px;top:842px;font-size:44px}
.about-text{left:632px;top:930px;width:458px;font-size:14px;line-height:32px;color:var(--muted);text-align:justify}
.about .btn{left:632px;top:1128px;width:185px;height:47px;box-shadow:0 0 0 2px #f2f2f2}

/* services */
.services-bg{left:0;top:1250px;width:1200px;height:1000px}
.services-ghost{top:1405px;font-size:80px}
.services-title{top:1438px;font-size:42px}
.card{width:304px;height:231px;background:#fff;box-shadow:0 2px 10px rgba(0,0,0,.08);text-align:center}
.card .icon{width:62px;height:62px;margin:32px auto 0;border:2.5px solid var(--red);border-radius:8px;position:relative}
.card .icon::after{content:"";position:absolute;left:12px;right:12px;top:24px;height:10px;border-top:2.5px solid var(--orange);border-bottom:2.5px solid var(--orange)}
.card h3{margin-top:20px;font-family:"Roboto",sans-serif;font-weight:500;font-size:21px;color:var(--ink)}
.card p{margin:16px auto 0;width:250px;font-size:14px;line-height:25px;color:var(--muted)}

/* philosophy */
.philo{left:0;top:2150px;width:1200px;height:410px}
.philo-mark{left:571px;top:2235px;width:58px;height:58px;border-radius:50%;background:#fff}
.philo-ghost{top:2275px;font-size:80px;color:rgba(255,255,255,.14)}
.philo-title{top:2316px;font-size:40px;color:#fff}
.philo-text{left:195px;top:2392px;width:810px;text-align:center;color:#fff;font-size:15px;line-height:32px}

/* testimonials */
.testi-ghost{top:2628px;font-size:82px}
.testi-title{top:2665px;font-size:46px}
.testi-sub{top:2740px;font-size:14px;color:var(--muted)}
.quote{width:302px;height:142px;background:#fff;box-shadow:0 2px 8px rgba(0,0,0,.08);padding:24px 22px 0;border:2px solid transparent}
.quote.active{border-color:var(--orange)}
.quote .mark{color:var(--red);font-size:22px;font-family:"Lato",sans-serif;font-weight:900;line-height:10px;height:10px}
.quote p{font-style:italic;font-size:14px;line-height:29px;color:var(--muted);text-align:justify;text-indent:44px}
.quote::after{content:"";position:absolute;left:44px;bottom:-18px;border-left:10px solid transparent;border-right:10px solid transparent;border-top:18px solid #fff}
.quote.active::after{border-top-color:var(--orange)}
.author{display:flex;align-items:center;gap:18px}
.avatar{width:52px;height:52px;border-radius:50%;background:linear-gradient(135deg,#c9d2db,#9aa6b2)}
.author b{display:block;color:var(--red);font-size:16px;font-weight:500}
.author span{display:block;margin-top:6px;font-size:12px;color:var(--muted)}
.divider{left:110px;top:3137px;width:980px;height:1px;background:var(--line)}

/* clients */
.clients-ghost{top:3205px;font-size:82px}
.clients-title{top:3241px;font-size:46px}
.clients-text{left:210px;top:3325px;width:780px;text-align:center;font-size:14px;line-height:25px;color:var(--muted)}
.client{top:3415px;width:177px;height:86px;border:2px solid #e2e2e2;display:flex;align-items:center;justify-content:center;gap:7px;font-family:"Roboto",sans-serif;font-size:17px;font-weight:500;color:#555}
.client i{width:14px;height:14px;background:#555;display:block}

/* footer */
.footer{left:0;top:3630px;width:1200px;height:569px}
.footer-logo{left:0;width:1200px;top:3735px;justify-content:center;font-size:44px;color:#fff}
.f-col{top:3853px;color:#fff}
.f-col h4{font-size:16px;font-weight:700;text-decoration:underline;text-underline-offset:4px;margin-bottom:20px}
.f-col li{font-size:13.5px;margin-bottom:16px;padding-left:20px;position:relative}
.f-col li::before{content:"»";position:absolute;left:0;top:-1px}
.f-col p{font-size:13px;line-height:21px}
.f-input{margin-top:14px;width:270px;height:36px;border:1px solid #fff;font-size:12px;padding:11px 10px}
.f-submit{margin-top:14px;width:100px;height:36px;border-radius:18px;background:var(--red);font-size:13px;font-weight:500;display:flex;align-items:center;justify-content:center}
.contact li{padding-left:53px;margin-bottom:18px;line-height:23px;font-size:13px}
.contact li::before{content:"";left:10px;top:2px;width:18px;height:18px;border:1.5px solid #fff;border-radius:50%}
.f-rule{top:4095px;height:1px;background:#555}
.socials{left:510px;top:4077px;display:flex;gap:12px}
.socials span{width:36px;height:36px;border:2px solid #fff;border-radius:50%;display:block}
.copyright{top:4147px;font-size:14.5px;color:#fff}
</style>
</head>
<body>

<header>
  <div class="abs topline"></div>
  <a class="abs logo site-logo" href="http://www.plovencast.example/index.html"><span class="logo-dot"></span>plovencast.net</a>
  <nav class="abs main-nav"><a>Home</a><a>About Us</a><a>Services</a><a>Clients</a><a>Contact Us</a></nav>
  <a class="abs login"><i></i>LOGIN</a>
</header>

<section class="abs hero">
  <h1 class="abs">Innovative &amp; High-Grade Software</h1>
  <p class="abs">One of our long term clients, Marrowlane have been using our services since 2001.</p>
  <a class="abs btn">READ MORE <span class="arrow"></span></a>
  <div class="abs hero-art" role="img" aria-label="Illustration of a person arranging cloud system windows"></div>
</section>
<svg class="abs hero-wave" style="top:640px" width="1200" height="82" viewBox="0 0 1200 82" aria-hidden="true"><path d="M0 82 C220 20 420 5 640 28 C860 52 1040 50 1200 82 Z" fill="#fff"/></svg>

<section class="about">
  <div class="abs about-art" role="img" aria-label="Illustration of a woman with desktop, tablet and phone screens"></div>
  <div class="abs ghost about-ghost">PLOVENCAST</div>
  <h2 class="abs title about-title">About Plovencast</h2>
  <p class="abs about-text">We build and run the back end of business systems for private and government clients: system support, security and cloud based applications. We are known for the quality of our work, fair rates and our individual approach to each customer. We help medium and large teams improve or upgrade the systems they already rely on.</p>
  <a class="abs btn">READ MORE <span class="arrow"></span></a>
</section>

<section class="services">
  <svg class="abs services-bg" width="1200" height="1000" viewBox="0 0 1200 1000" aria-hidden="true"><path d="M0 50 C250 140 520 40 760 20 C960 5 1100 40 1200 60 L1200 1000 L0 1000 Z" fill="var(--soft)"/></svg>
  <div class="abs ghost center services-ghost">Our Services</div>
  <h2 class="abs title center services-title">Our Services</h2>
  <article class="abs card" style="left:110px;top:1557px"><div class="icon"></div><h3>SYSTEM SUPPORT</h3><p>Round the clock care that keeps your core systems stable.</p></article>
  <article class="abs card" style="left:448px;top:1557px"><div class="icon"></div><h3>SECURITY</h3><p>Audits, hardening and monitoring to protect your data.</p></article>
  <article class="abs card" style="left:786px;top:1557px"><div class="icon"></div><h3>CLOUD APPS</h3><p>Cloud based applications built to scale with your business.</p></article>
  <article class="abs card" style="left:110px;top:1820px"><div class="icon"></div><h3>SYSTEM UPGRADES</h3><p>Modernise legacy platforms without disrupting your work.</p></article>
  <article class="abs card" style="left:448px;top:1820px"><div class="icon"></div><h3>DATA MANAGEMENT</h3><p>Reliable storage, backup and recovery for critical data.</p></article>
  <article class="abs card" style="left:786px;top:1820px"><div class="icon"></div><h3>HOSTING SOLUTIONS</h3><p>Secure, managed hosting for private and public sector teams.</p></article>
</section>

<section>
  <svg class="abs philo" width="1200" height="410" viewBox="0 0 1200 410" aria-hidden="true">
    <defs><linearGradient id="philoGrad" x1="0" x2="1"><stop offset="0" stop-color="#e8333f"/><stop offset="1" stop-color="#ff7a12"/></linearGradient></defs>
    <path d="M0 90 C300 40 650 0 1000 10 C1100 14 1160 20 1200 30 L1200 410 L0 410 Z" fill="url(#philoGrad)"/>
  </svg>
  <div class="abs philo-mark"></div>
  <div class="abs ghost center philo-ghost">PHILOSOPHY</div>
  <h2 class="abs title center philo-title">Philosophy</h2>
  <p class="abs philo-text">As system engineers, we understand that secure and dependable back end systems are a vital part of every modern organisation. This is why our support, security and cloud team work closely with all of our clients to make sure their systems stay fast, safe and ready to grow.</p>
</section>

<section>
  <div class="abs ghost center testi-ghost">OUR TESTIMONIALS</div>
  <h2 class="abs title center testi-title">Our Testimonials</h2>
  <p class="abs center testi-sub">Nor again is there anyone who loves or pursues or desires to obtain pain of itself because it is pain.</p>

  <blockquote class="abs quote" style="left:110px;top:2808px"><div class="mark">“</div><p>Lorem ipsum dolor sit amet, consectetur adipiscing elit, sed do eiusmod tempor incididunt</p></blockquote>
  <blockquote class="abs quote active" style="left:450px;top:2808px"><div class="mark">“</div><p>Lorem ipsum dolor sit amet, consectetur adipiscing elit, sed do eiusmod tempor incididunt</p></blockquote>
  <blockquote class="abs quote" style="left:788px;top:2808px"><div class="mark">“</div><p>Lorem ipsum dolor sit amet, consectetur adipiscing elit, sed do eiusmod tempor incididunt</p></blockquote>

  <div class="abs author" style="left:112px;top:2978px"><div class="avatar" role="img" aria-label="Portrait of client Tomas Verlo"></div><div><b>Tomas Verlo</b><span>Lorem ipsum dolor sit amet</span></div></div>
  <div class="abs author" style="left:448px;top:2978px"><div class="avatar" role="img" aria-label="Portrait of client Ines Carrow"></div><div><b>Ines Carrow</b><span>Lorem ipsum dolor sit amet</span></div></div>
  <div class="abs author" style="left:790px;top:2978px"><div class="avatar" role="img" aria-label="Portrait of client Aldo Brinn"></div><div><b>Aldo Brinn</b><span>Lorem ipsum dolor sit amet</span></div></div>
</section>

<div class="abs divider"></div>

<section>
  <div class="abs ghost center clients-ghost">OUR CLIENTS</div>
  <h2 class="abs title center clients-title">Our Clients</h2>
  <p class="abs clients-text">Lorem ipsum dolor sit amet, consectetur adipiscing elit, sed do eiusmod tempor incididunt ut labore et dolore magna aliqua. Ut enim ad minim veniam nostrud exercitation ullamco laboris nisi.</p>
  <div class="abs client" style="left:110px">Harbourview Clinic</div>
  <div class="abs client" style="left:311px">Kindred Aid</div>
  <div class="abs client" style="left:512px"><i></i>Slatewell</div>
  <div class="abs client" style="left:712px">Norvale Group</div>
  <div class="abs client" style="left:912px">Brightpath Skills</div>
</section>

<footer>
  <svg class="abs footer" width="1200" height="569" viewBox="0 0 1200 569" aria-hidden="true">
    <path d="M0 90 C250 20 450 0 600 0 C750 0 950 20 1200 90 L1200 569 L0 569 Z" fill="var(--red)"/>
    <path d="M0 100 C250 30 450 12 600 12 C750 12 950 30 1200 100 L1200 569 L0 569 Z" fill="var(--footer)"/>
  </svg>
  <div class="abs logo footer-logo"><span class="logo-dot"></span>plovencast.net</div>

  <div class="abs f-col" style="left:112px"><h4>COMPANY</h4><ul><li>Home</li><li>About Us</li><li>Our Services</li><li>Solutions</li></ul></div>
  <div class="abs f-col" style="left:289px"><h4>RESOURCES</h4><ul><li>Contact Us</li><li>Book A Callback</li><li>FAQs</li><li>Terms &amp; Conditions</li></ul></div>
  <div class="abs f-col" style="left:507px"><h4>JOIN OUR NEWSLETTER</h4><p>Sign up for our newsletter to stay up-to-date<br>with our Company Informations</p><div class="f-input">Email Address</div><div class="f-submit">SUBMIT</div></div>
  <div class="abs f-col contact" style="left:859px"><h4>CONTACT DETAILS</h4><ul><li>48 Fenwick Lane, Suite 9<br>Eastmoor, Norland 41</li><li>(+1) 555 014 2290</li><li>info@plovencast.example</li></ul></div>

  <div class="abs f-rule" style="left:110px;width:385px"></div>
  <div class="abs f-rule" style="left:705px;width:385px"></div>
  <div class="abs socials" aria-label="Social links"><span></span><span></span><span></span><span></span></div>
  <p class="abs center copyright">Copyrights © 2019 Plovencast.net. All Rights Reserved &nbsp; | &nbsp; Privacy Policy</p>
</footer>

</body>
</html>
```